Building company buisness cards

We are looking for a sharp modern new look for our business cards.We are a New Zealand based company that specialises in house and land packages.We have attached a photo of the current logo and would like to see if it can be improved somehow if needed.We are open to any colours but we have chosen Black and White at this stage. Feel free to change the font and make the logo smarter looking.Play with the colours and see what looks best.We want a card that looks so good know one will want to throw it away!

Target Market(s)

Building profesonals, home buyers

Industry/Entity Type

Building

Contact Information for Business Card

Garrick Tenwood
0275390628
garrickt@hartvale.co.nz

Font styles to use
Serif
Sans Serif

Colors

Designer to choose colors to be used in the design.

Requirements
Must have
• Just the logo on one side and details on the other
• Clean simple looking card
Nice to have
• Round corners and detail like raised or spot UV
• Something that stands out
Should not have
• To title needed, Director etc

```html
<!DOCTYPE html>
<html lang="en">
<head>
<meta charset="utf-8">
<title>Hartvale Business Cards</title>
<link href="https://fonts.googleapis.com/css2?family=Archivo:wght@500;600;700;800&display=swap" rel="stylesheet">
<style>
  :root {
    --navy: #1d2858;
    --orange: #f0a030;
    --ink-grey: #555559;
    --paper: #ffffff;
    --backdrop: #dedede;
  }
  html, body {
    margin: 0;
    padding: 0;
    width: 1125px;
    height: 1200px;
    overflow: hidden;
    background: var(--backdrop);
    font-family: "Archivo", Arial, sans-serif;
  }
  .canvas {
    position: relative;
    width: 1125px;
    height: 1200px;
  }
  .card {
    position: absolute;
    left: 156px;
    width: 825px;
    height: 471px;
    border-radius: 26px;
    overflow: hidden;
  }
  .card-front {
    top: 106px;
    background: var(--paper);
  }
  .card-back {
    top: 639px;
    background: var(--navy);
  }
  .brand {
    position: absolute;
    display: flex;
    align-items: center;
    gap: 20px;
  }
  .brand-front {
    left: 48px;
    top: 58px;
  }
  .brand-name {
    font-weight: 800;
    font-size: 58px;
    line-height: 1;
    letter-spacing: 1px;
  }
  .brand-front .brand-name { color: var(--navy); }
  .brand-ring {
    display: block;
  }
  .contact {
    position: absolute;
    left: 48px;
    top: 312px;
  }
  .contact-name {
    margin: 0 0 20px;
    font-weight: 700;
    font-size: 28px;
    color: var(--navy);
  }
  .contact-phone {
    margin: 0 0 8px;
    font-weight: 600;
    font-size: 19px;
    letter-spacing: 0.5px;
    color: var(--ink-grey);
  }
  .contact-email {
    margin: 0;
    font-weight: 500;
    font-size: 17px;
    color: var(--ink-grey);
  }
  .web-front {
    position: absolute;
    right: 46px;
    top: 392px;
    margin: 0;
    font-weight: 600;
    font-size: 17px;
    letter-spacing: 4px;
    color: var(--ink-grey);
  }
  .brand-back {
    left: 0;
    right: 0;
    top: 206px;
    justify-content: center;
  }
  .brand-back .brand-name { color: var(--paper); }
  .web-back {
    position: absolute;
    left: 0;
    right: 0;
    top: 400px;
    margin: 0;
    text-align: center;
    font-weight: 500;
    font-size: 19px;
    letter-spacing: 9px;
    color: var(--paper);
  }
</style>
</head>
<body>
<main class="canvas">
  <section class="card card-front" aria-label="Business card front">
    <div class="brand brand-front">
      <span class="brand-name">HARTVALE</span>
      <svg class="brand-ring" width="64" height="64" viewBox="0 0 64 64" aria-hidden="true">
        <circle cx="32" cy="32" r="29" fill="none" stroke="var(--orange)" stroke-width="4"/>
      </svg>
    </div>
    <div class="contact">
      <p class="contact-name">Garrick Tenwood</p>
      <p class="contact-phone">0275390628</p>
      <p class="contact-email">garrickt@hartvale.co.nz</p>
    </div>
    <p class="web-front">www.hartvale.co.nz</p>
  </section>

  <section class="card card-back" aria-label="Business card back">
    <div class="brand brand-back">
      <span class="brand-name">HARTVALE</span>
      <svg class="brand-ring" width="64" height="64" viewBox="0 0 64 64" aria-hidden="true">
        <circle cx="32" cy="32" r="29" fill="none" stroke="var(--paper)" stroke-width="4"/>
      </svg>
    </div>
    <p class="web-back">www.Hartvale.co.nz</p>
  </section>
</main>
</body>
</html>
```